Verdant Ledger - Paid Surveys publisher portal

• Homepage
• Blank Sub Page (Where content goes in between the header/footer)
• Publisher Application Page, complete with Form
• Survey Wall page

Sites that are in a similar vertical that have interesting designs:
rovabin.com
quillmarsh.com
dovek.com
tarn.io

This is a business-to-business site, and needs to have this type of feel to it. Focus on generating revenue, offer completion, paid surveys is the market.

Format: HTML/CSS

Link to current version of application, and form:
https://gridwaveform.brokelqest.com
https://gridwaveform.brokelqest.com/apply
https://gridwaveform.brokelqest.com/panel/4/morvath_user

Please note that we are changing the brand of this project, the name will be determined shortly but everything else remains. It will likely be Verdant Ledger instead of GridWaveform. We will confirm.

Industry/Entity Type

Market Research

Coding

Coded - Design and coding required

Number of Pages Required

4 page

Font styles to use
Sans Serif

Colors

Designer to choose colors to be used in the design.

```html
<!DOCTYPE html>
<html lang="en">
<head>
<meta charset="utf-8">
<title>GridWaveform — Paid Surveys Publisher Portal</title>
<link href="https://fonts.googleapis.com/css2?family=Mulish:wght@400;600;700&family=Open+Sans:wght@400;600;700&display=swap" rel="stylesheet">
<style>
:root{
  --blue:#2a8fd8;
  --btn-blue:#2d8cd6;
  --green:#3fb58a;
  --red:#e84c4c;
  --ink:#222;
  --text:#444;
  --muted:#777;
  --band:#eef6fb;
  --footer:#2b394c;
  --footer-text:#aeb8c5;
  --line:#cfcfcf;
}
*{margin:0;padding:0;box-sizing:border-box}
html,body{width:1200px;height:2715px;overflow:hidden;background:#fff}
body{position:relative;font-family:"Open Sans",Arial,sans-serif;color:var(--text)}
.abs{position:absolute}
a{color:inherit;text-decoration:none}

/* header */
.site-header{left:0;top:0;width:1200px;height:82px;background:#fff}
.brand{left:132px;top:16px;display:flex;align-items:center;gap:12px;font-family:"Mulish",sans-serif;font-size:31px;color:#333;font-weight:400}
.brand-dot{width:48px;height:48px;border-radius:50%;background:var(--red)}
.main-nav a{position:absolute;top:33px;font-size:14px;color:#333}
.main-nav a.active{color:var(--red)}
.login-btn{left:928px;top:16px;width:140px;height:51px;background:var(--btn-blue);color:#fff;font-size:17px;display:flex;align-items:center;justify-content:center;border-radius:2px}

/* hero */
.hero{left:0;top:82px;width:1200px;height:533px;background:linear-gradient(100deg,#6b6660 0%,#8d8a84 22%,#c9c6c0 45%,#e6e4e0 65%,#f1f0ee 100%)}
.hero-title{right:132px;top:260px;text-align:right;font-family:"Mulish",sans-serif;font-size:46px;line-height:52px;color:#3a3a3a;font-weight:400}
.btn-green{background:var(--green);color:#fff;display:flex;align-items:center;justify-content:center;font-size:16px;border-radius:2px}
.hero-btn{left:912px;top:377px;width:156px;height:49px}
.arrow{width:30px;height:30px;border-radius:50%;background:#333;display:flex;align-items:center;justify-content:center}

/* intro */
.section-title{width:1200px;left:0;text-align:center;font-family:"Mulish",sans-serif;color:var(--blue);font-weight:400}
.intro-title{top:684px;font-size:33px}
.intro-text{left:132px;top:733px;width:936px;text-align:center;font-size:13px;line-height:24px;color:#333}
.checklist{left:132px;top:872px;list-style:none}
.checklist li{font-size:17px;font-weight:600;color:#222;height:40px;display:flex;align-items:center;gap:12px}
.learn-btn{left:132px;top:1086px;width:116px;height:51px}
.dashboard{left:619px;top:860px;width:449px;height:302px;border:4px solid #ddd;background:linear-gradient(180deg,#f3f4f6 0%,#e9ecef 100%)}

/* stats */
.stats{left:0;top:1243px;width:1200px;height:223px;background:var(--band)}
.stat{position:absolute;top:70px;width:240px;text-align:center;color:var(--red)}
.stat-num{font-family:"Mulish",sans-serif;font-size:39px;font-weight:700;line-height:46px}
.stat-label{font-size:16px;margin-top:4px}

/* news */
.news-title{top:1530px;font-size:33px}
.news-card{top:1585px;width:298px;height:144px;border:1px solid var(--line);padding:18px 20px}
.news-card h3{font-family:"Open Sans",sans-serif;font-size:16.5px;font-weight:400;color:#222;margin-bottom:6px}
.news-card time{font-size:11.5px;color:#555;display:block;margin-bottom:10px}
.news-card p{font-size:10.5px;line-height:18px;color:#444;height:54px;overflow:hidden}
.view-all{left:552px;top:1750px;width:98px;height:38px;border:1px solid #aaa;font-size:11px;letter-spacing:.5px;color:#444;display:flex;align-items:center;justify-content:center}

/* testimonials */
.testimonials{left:0;top:1868px;width:1200px;height:367px;background:linear-gradient(90deg,#cfd3d4 0%,#e7eaeb 35%,#dcdad6 60%,#b9b3ad 80%,#d6d9da 100%)}
.testi-title{left:132px;top:1946px;font-family:"Mulish",sans-serif;font-size:33px;color:var(--blue);font-weight:400}
.testi-box{left:132px;top:1996px;width:578px;height:152px;background:rgba(255,255,255,.95);padding:18px 24px;font-size:15px;line-height:26px;color:#444}
.testi-box cite{display:block;color:var(--blue);font-style:normal;margin-top:6px}
.chev{width:24px;height:24px}

/* partners */
.partners-title{left:0;top:2310px;width:1200px;text-align:center;font-size:16px;font-weight:600;color:#222}
.partner{top:2374px;width:130px;text-align:center;font-family:"Open Sans",sans-serif;font-size:17px;font-weight:600;color:#222;line-height:30px}

/* footer */
.site-footer{left:0;top:2492px;width:1200px;height:223px;background:var(--footer);color:var(--footer-text)}
.foot-brand{left:132px;top:44px;display:flex;align-items:center;gap:10px;font-family:"Mulish",sans-serif;font-size:25px;color:#c9d1db}
.foot-brand .brand-dot{width:38px;height:38px;background:#c9d1db}
.copyright{left:132px;top:104px;font-size:11.5px;line-height:26px}
.foot-head{top:40px;font-size:16px;font-weight:600;color:#fff}
.foot-col{top:76px;list-style:none;font-size:11.5px;line-height:26px}
.social{top:82px;width:32px;height:32px;border:1px solid #8e9aa9;border-radius:50%}
</style>
</head>
<body>

<header class="site-header abs">
  <div class="brand abs"><span class="brand-dot"></span>GridWaveform</div>
  <nav class="main-nav">
    <a class="active" style="left:485px">Affiliates</a>
    <a style="left:568px">Advertisers</a>
    <a style="left:666px">About</a>
    <a style="left:735px">FAQ</a>
    <a style="left:796px">Blog</a>
    <a style="left:856px">Support</a>
  </nav>
  <a class="login-btn abs">Member Login</a>
</header>

<section class="hero abs" role="img" aria-label="Photo of a smiling man working on a laptop on a living room sofa"></section>
<h1 class="hero-title abs">Curabitur venenatis<br>lacinia ornare</h1>
<a class="btn-green hero-btn abs">Get Started Now</a>
<span class="arrow abs" style="left:47px;top:332px"><svg width="12" height="12" viewBox="0 0 12 12"><path d="M8 1 3 6l5 5" stroke="#fff" stroke-width="2.4" fill="none"/></svg></span>
<span class="arrow abs" style="left:1122px;top:332px"><svg width="12" height="12" viewBox="0 0 12 12"><path d="M4 1l5 5-5 5" stroke="#fff" stroke-width="2.4" fill="none"/></svg></span>

<h2 class="section-title intro-title abs">Maecenas vel tortor accumsan quam varius</h2>
<p class="intro-text abs">Aenean facilisis tincidunt lectus, id dictum nisi luctus eget. Vivamus efficitur ex condimentum, malesuada eros eget, feugiat nibh. Sed tellus ex, imperdiet eget gravida sit amet, volutpat eget turpis. In nec ultricies est. Etiam mattis augue vehicula odio posuere, sit amet tempus lectus luctus. Nulla facilisi. Etiam vel massa elementum, bibendum tellus venenatis, feugiat massa. Curabitur venenatis lacinia ornare.</p>

<ul class="checklist abs">
  <li><svg width="16" height="14" viewBox="0 0 16 14"><path d="M1.5 7.5 6 12 14.5 2" stroke="#222" stroke-width="3" fill="none"/></svg>Aliquam dignissim elit nec mauris porta.</li>
  <li><svg width="16" height="14" viewBox="0 0 16 14"><path d="M1.5 7.5 6 12 14.5 2" stroke="#222" stroke-width="3" fill="none"/></svg>Ut eu tellus scelerisque, tempor ex ac, sollicitudin dui.</li>
  <li><svg width="16" height="14" viewBox="0 0 16 14"><path d="M1.5 7.5 6 12 14.5 2" stroke="#222" stroke-width="3" fill="none"/></svg>Nulla porttitor nibh ut mi feugiat rhoncus quis in ante.</li>
  <li><svg width="16" height="14" viewBox="0 0 16 14"><path d="M1.5 7.5 6 12 14.5 2" stroke="#222" stroke-width="3" fill="none"/></svg>Nam tempus augue eu ante lacinia.</li>
  <li><svg width="16" height="14" viewBox="0 0 16 14"><path d="M1.5 7.5 6 12 14.5 2" stroke="#222" stroke-width="3" fill="none"/></svg>Maecenas sed nibh sed nisi tristique pharetra.</li>
</ul>
<a class="btn-green learn-btn abs">Learn More</a>

<div class="dashboard abs" role="img" aria-label="Screenshot of the publisher dashboard with stats, charts and a project table"></div>

<section class="stats abs">
  <div class="stat" style="left:116px"><div class="stat-num">1,815</div><div class="stat-label">Nam elementum velit</div></div>
  <div class="stat" style="left:359px"><div class="stat-num">68+</div><div class="stat-label">Maecenas sed nibh</div></div>
  <div class="stat" style="left:601px"><div class="stat-num">321,658</div><div class="stat-label">Vestibulum ut velit</div></div>
  <div class="stat" style="left:844px"><div class="stat-num">245</div><div class="stat-label">Quisque blandit elit</div></div>
</section>

<h2 class="section-title news-title abs">News</h2>
<article class="news-card abs" style="left:132px">
  <h3>Fusce sollicitudin lorem et luctus</h3>
  <time>6 September, 2018</time>
  <p>Possibilité de typer les champs personnalisés, refonte du moteur de recherche d'événements et amélioration des performances de l'application</p>
</article>
<article class="news-card abs" style="left:451px">
  <h3>In tristique tristique nulla</h3>
  <time>6 September, 2018</time>
  <p>Création de plusieurs plannings par ressource, superposition d'événements à la même heure, nouveau module de suivi des heures travaillées et</p>
</article>
<article class="news-card abs" style="left:770px">
  <h3>Maecenas vel tortor accumsan</h3>
  <time>6 September, 2018</time>
  <p>Création d'événements de moins de 15 minutes et multi-participants, refonte du moteur de recherche de ressources, amélioration du pack mobilité,</p>
</article>
<a class="view-all abs">VIEW ALL</a>

<section class="testimonials abs" role="img" aria-label="Photo of a smiling woman in a bright office"></section>
<h2 class="testi-title abs">Testimonials</h2>
<blockquote class="testi-box abs">" Proin placerat dapibus gravida. In tristique tristique nulla eget hendrerit.<br>Maecenas vel tortor accumsan quam varius imperdiet vel eget elit.<br>Aenean facilisis tincidunt lectus, id dictum nisi luctus eget. "<cite>- Madison, City</cite></blockquote>
<svg class="chev abs" style="left:44px;top:2040px" viewBox="0 0 24 24"><path d="M15 3 6 12l9 9" stroke="#555" stroke-width="2" fill="none"/></svg>
<svg class="chev abs" style="left:1132px;top:2040px" viewBox="0 0 24 24"><path d="M9 3l9 9-9 9" stroke="#555" stroke-width="2" fill="none"/></svg>

<h3 class="partners-title abs">Duis hendrerit arcu egestas vulputate porttitor</h3>
<div class="partner abs" style="left:124px">Orrin Vale</div>
<div class="partner abs" style="left:267px">Lumé</div>
<div class="partner abs" style="left:405px">Tessary Hall</div>
<div class="partner abs" style="left:544px">marco pellan</div>
<div class="partner abs" style="left:686px">KIVARO</div>
<div class="partner abs" style="left:827px">Brightmoor</div>
<div class="partner abs" style="left:968px">Quarrel</div>

<footer class="site-footer abs">
  <div class="foot-brand abs"><span class="brand-dot"></span>GridWaveform</div>
  <p class="copyright abs">Copyright © 2018 GridWaveform.<br>All rights reserved.</p>

  <h4 class="foot-head abs" style="left:405px">Links</h4>
  <ul class="foot-col abs" style="left:405px"><li>Affiliates</li><li>Advertisers</li><li>About</li><li>FAQ</li></ul>
  <ul class="foot-col abs" style="left:486px"><li>Blog</li><li>Support</li><li>Member Login</li><li>Register</li></ul>

  <h4 class="foot-head abs" style="left:664px">Pellentesque</h4>
  <ul class="foot-col abs" style="left:664px"><li>Integer</li><li>Nam elementum</li><li>Maecenas</li><li>Vestibulum</li></ul>
  <ul class="foot-col abs" style="left:775px"><li>Quisque</li><li>Duis id</li><li>Aliquam ac</li><li>Donec</li></ul>

  <h4 class="foot-head abs" style="left:937px">Follow us on</h4>
  <span class="social abs" style="left:938px"></span>
  <span class="social abs" style="left:986px"></span>
  <span class="social abs" style="left:1034px"></span>
</footer>

</body>
</html>
```